IT Company requires new Business Card design.

Over the years we have had a few different business card designs. We are now due for new cards across the board for all staff. We felt this would be a good time to start fresh with a new design. Our traditional card simply had our details on the front, and a list of services on the back. We don't particularly need the list of services, we have had cards where the only thing on the rear of the card was our logo.
Feel free to be creative, we would like our tag line "Complete IT Management" to appear at some point, doesn't necessarily have to be with the logo.
I have attached samples and drafts of various previous cards we have used over the years.

```html
<!DOCTYPE html>
<html lang="en">
<head>
<meta charset="utf-8">
<title>Ridge Networking – Business Card</title>
<link rel="stylesheet" href="https://fonts.googleapis.com/css2?family=Archivo:wght@800&family=Open+Sans:wght@400;700&display=swap">
<style>
  :root {
    --page: #e9e9e9;
    --card: #ffffff;
    --slate: #5b6873;
    --charcoal: #3e3f41;
    --ink-light: #ffffff;
    --url-ink: #333333;
  }
  * { box-sizing: border-box; margin: 0; padding: 0; }
  html, body {
    width: 1034px; height: 1200px; overflow: hidden;
    background: var(--page);
    font-family: "Open Sans", Arial, sans-serif;
  }
  .card {
    position: absolute; left: 67px; width: 900px; height: 515px;
    background: var(--card);
    box-shadow: 0 3px 10px rgba(0,0,0,0.25);
    overflow: hidden;
  }
  .card--front { top: 65px; }
  .card--back { top: 621px; }

  /* front */
  .brand {
    position: absolute; top: 78px; left: 0; right: 0;
    display: flex; justify-content: center; align-items: center; gap: 26px;
  }
  .brand__square { width: 150px; height: 150px; background: var(--slate); }
  .brand__name {
    font-family: "Archivo", "Arial Black", sans-serif; font-weight: 800;
    color: var(--slate); line-height: 0.98; font-size: 64px; letter-spacing: 1px;
  }
  .name-bar {
    position: absolute; top: 319px; left: 0; right: 0; height: 51px;
    background: var(--charcoal); color: var(--ink-light);
    display: flex; align-items: center; justify-content: center; gap: 8px;
  }
  .name-bar__name { font-weight: 700; font-size: 24px; }
  .name-bar__role { font-size: 20px; }
  .contact-panel {
    position: absolute; top: 376px; left: 0; right: 0; bottom: 0;
    background: var(--slate); color: var(--ink-light);
    display: flex; flex-direction: column; align-items: center; justify-content: center; gap: 8px;
    font-size: 20px;
  }
  .contact-row { display: flex; align-items: center; gap: 22px; }
  .contact-item { display: flex; align-items: center; gap: 8px; }
  .contact-item svg { width: 20px; height: 20px; fill: var(--ink-light); }

  /* back */
  .back-lockup {
    position: absolute; top: 125px; left: 0; right: 0; text-align: center;
    font-family: "Archivo", "Arial Black", sans-serif; font-weight: 800; color: var(--slate);
  }
  .back-lockup__line1 { font-size: 112px; line-height: 0.95; letter-spacing: 4px; }
  .back-lockup__line2 { font-size: 66px; line-height: 1.05; letter-spacing: 2px; }
  .tagline {
    position: absolute; top: 335px; left: 0; right: 0; text-align: center;
    font-size: 27px; letter-spacing: 7px; color: var(--slate);
  }
  .web-address {
    position: absolute; top: 446px; left: 0; right: 0; text-align: center;
    font-size: 25px; letter-spacing: 3px; color: var(--url-ink);
  }
</style>
</head>
<body>
  <section class="card card--front">
    <div class="brand">
      <div class="brand__square"></div>
      <div class="brand__name">RIDGE<br>NETWORKING</div>
    </div>
    <div class="name-bar">
      <span class="name-bar__name">Mark Ellison,</span>
      <span class="name-bar__role">Operation Manager</span>
    </div>
    <div class="contact-panel">
      <div class="contact-row">
        <span class="contact-item">
          <svg viewBox="0 0 24 24" aria-hidden="true"><path d="M6.6 10.8a15 15 0 0 0 6.6 6.6l2.2-2.2c.3-.3.7-.4 1-.2 1.1.4 2.3.6 3.6.6.6 0 1 .4 1 1V20c0 .6-.4 1-1 1A17 17 0 0 1 3 4c0-.6.4-1 1-1h3.5c.6 0 1 .4 1 1 0 1.3.2 2.5.6 3.6.1.3 0 .7-.2 1z"/></svg>
          08 9555 0142
        </span>
        <span class="contact-item">
          <svg viewBox="0 0 24 24" aria-hidden="true"><path d="M7 1h10a2 2 0 0 1 2 2v18a2 2 0 0 1-2 2H7a2 2 0 0 1-2-2V3a2 2 0 0 1 2-2zm0 3v14h10V4zm5 15.5a1.2 1.2 0 1 0 0 2.4 1.2 1.2 0 0 0 0-2.4z"/></svg>
          0400 555 817
        </span>
        <span class="contact-item">
          <svg viewBox="0 0 24 24" aria-hidden="true"><path d="M6 2h10v6H6zM3 9h18a1 1 0 0 1 1 1v8a1 1 0 0 1-1 1h-3v3H6v-3H3a1 1 0 0 1-1-1v-8a1 1 0 0 1 1-1zm5 7v4h8v-4z"/></svg>
          08 9555 0142
        </span>
      </div>
      <div class="contact-row">
        <span class="contact-item">
          <svg viewBox="0 0 24 24" aria-hidden="true"><path d="M2 5h20v14H2zm2 2v.5l8 5 8-5V7zm0 2.8V17h16V9.8l-8 5z"/></svg>
          mark@ridgenetworking.com.au
        </span>
        <span class="contact-item">
          <svg viewBox="0 0 24 24" aria-hidden="true"><path d="M12 2a10 10 0 1 0 0 20 10 10 0 0 0 0-20zm6.9 6h-2.9a15 15 0 0 0-1.4-3.9A8 8 0 0 1 18.9 8zM12 4c.8 1.1 1.5 2.5 1.9 4h-3.8c.4-1.5 1.1-2.9 1.9-4zM4.3 14a8 8 0 0 1 0-4h3.4a16 16 0 0 0 0 4zm.8 2h2.9c.3 1.4.8 2.7 1.4 3.9A8 8 0 0 1 5.1 16zM8 8H5.1a8 8 0 0 1 4.3-3.9C8.8 5.3 8.3 6.6 8 8zm4 12c-.8-1.1-1.5-2.5-1.9-4h3.8c-.4 1.5-1.1 2.9-1.9 4zm2.3-6H9.7a14 14 0 0 1 0-4h4.6a14 14 0 0 1 0 4zm.3 5.9c.6-1.2 1.1-2.5 1.4-3.9h2.9a8 8 0 0 1-4.3 3.9zm1.7-5.9a16 16 0 0 0 0-4h3.4a8 8 0 0 1 0 4z"/></svg>
          www.ridgenetworking.com.au
        </span>
      </div>
      <div class="contact-row">
        <span class="contact-item">Unit 7 22 Harbour Road, Bibra Lake WA 6163</span>
      </div>
    </div>
  </section>

  <section class="card card--back">
    <div class="back-lockup">
      <div class="back-lockup__line1">RIDGE</div>
      <div class="back-lockup__line2">NETWORKING</div>
    </div>
    <div class="tagline">COMPLETE IT MANAGEMENT</div>
    <div class="web-address">www.ridgenetworking.com.au</div>
  </section>
</body>
</html>
```